Oil and Gas Exploration and Production company needs a business card design

We need a business card design using our logo and colors in the logo. We want a mainstream design.

```html
<!DOCTYPE html>
<html lang="en">
<head>
<meta charset="utf-8">
<title>Solara Oil &amp; Gas — Business Card</title>
<link rel="stylesheet" href="https://fonts.googleapis.com/css2?family=Roboto+Slab:wght@400;700;900&family=Roboto:wght@300;400&display=swap">
<style>
  :root {
    --gold: #c99a2c;
    --gold-deep: #b8881f;
    --ink: #141414;
    --paper: #ffffff;
    --stage: #ecebe8;
    --muted: #f1f1f1;
  }
  * { box-sizing: border-box; margin: 0; padding: 0; }
  html, body { width: 1200px; height: 911px; overflow: hidden; }
  body {
    background: var(--stage);
    font-family: "Roboto", Arial, sans-serif;
    position: relative;
  }
  .card {
    position: absolute;
    top: 301px;
    width: 540px;
    height: 309px;
    border-radius: 22px;
    overflow: hidden;
    box-shadow: 0 6px 18px rgba(0,0,0,.18);
  }
  .card-front { left: 40px; background: var(--paper); }
  .card-back { left: 620px; background: var(--gold); }

  .front-shape { position: absolute; inset: 0; width: 100%; height: 100%; }

  .brand {
    position: absolute;
    right: 34px;
    top: 96px;
    display: flex;
    align-items: center;
    gap: 12px;
  }
  .brand-dot {
    width: 30px; height: 30px; border-radius: 50%;
    background: var(--gold);
  }
  .brand-name {
    font-family: "Roboto Slab", Georgia, serif;
    font-weight: 900;
    color: var(--ink);
    font-size: 34px;
    line-height: 1;
  }
  .brand-name small { display: block; font-size: 19px; letter-spacing: 2px; margin-top: 6px; }

  .contact-block {
    position: absolute;
    left: 30px;
    top: 40px;
    color: var(--paper);
  }
  .person-name {
    font-family: "Roboto Slab", Georgia, serif;
    font-weight: 700;
    color: var(--gold);
    font-size: 22px;
  }
  .person-role {
    font-family: "Roboto Slab", Georgia, serif;
    font-size: 13px;
    margin-top: 2px;
  }
  .address {
    font-size: 12px;
    font-weight: 300;
    line-height: 1.45;
    margin-top: 20px;
  }
  .contact-list {
    list-style: none;
    margin-top: 14px;
    font-size: 12px;
    font-weight: 300;
    line-height: 1.55;
  }
  .contact-list li { display: flex; align-items: center; gap: 8px; }
  .contact-list svg { width: 11px; height: 11px; fill: var(--gold); flex: none; }

  .back-brand {
    position: absolute;
    left: 50%; top: 50%;
    transform: translate(-50%, -50%);
    display: flex; align-items: center; gap: 14px;
  }
  .back-brand .brand-dot { background: var(--ink); width: 40px; height: 40px; }
  .back-brand .brand-name { font-size: 38px; }

  .back-web {
    position: absolute;
    left: 30px;
    top: 50%;
    transform: translate(-50%, -50%) rotate(90deg);
    transform-origin: center;
    margin-left: 8px;
    color: var(--paper);
    font-size: 11px;
    letter-spacing: 4px;
    white-space: nowrap;
  }
</style>
</head>
<body>
  <section class="card card-front">
    <svg class="front-shape" viewBox="0 0 540 309" preserveAspectRatio="none" aria-hidden="true">
      <path d="M0 0 H250 C300 90 300 220 262 309 H0 Z" fill="var(--gold)"/>
      <path d="M0 0 H236 C284 90 284 220 248 309 H0 Z" fill="var(--ink)"/>
    </svg>

    <div class="contact-block">
      <div class="person-name">Daniel Brooks</div>
      <div class="person-role">CEO/Founder</div>
      <p class="address">1420 Ridgeview Road<br>Fairbanks, Alaska 99701</p>
      <ul class="contact-list">
        <li><svg viewBox="0 0 12 12"><path d="M2 1h3l1 3-2 1c1 2 2 3 4 4l1-2 3 1v3c-6 0-10-4-10-10z"/></svg>907 555 0142</li>
        <li><svg viewBox="0 0 12 12"><rect x="3" y="0" width="6" height="12" rx="1"/></svg>907 555 0187</li>
        <li><svg viewBox="0 0 12 12"><rect x="1" y="3" width="10" height="7"/><rect x="3" y="0" width="6" height="3"/></svg>907 555 0193</li>
        <li><svg viewBox="0 0 12 12"><path d="M0 2h12v8H0z M0 2l6 5 6-5" /></svg>info@solaraoilgas.com</li>
        <li><svg viewBox="0 0 12 12"><circle cx="6" cy="6" r="6"/></svg>www.solaraoilgas.com</li>
      </ul>
    </div>

    <div class="brand">
      <span class="brand-dot"></span>
      <div class="brand-name">Solara<small>OIL &amp; GAS</small></div>
    </div>
  </section>

  <section class="card card-back">
    <div class="back-web">www.solaraoilgas.com</div>
    <div class="back-brand">
      <span class="brand-dot"></span>
      <div class="brand-name">Solara</div>
    </div>
  </section>
</body>
</html>
```